11 month inspection POST CARD for Pinecrest Home Inspections

a post card size flyer to new home owners from Pinecrest Home Inspections.
Use text from this. front and back if needed.
Pinecrest Home Inspections
352-781-6094
www.PinecrestHomeInspections.com
Your Trusted Home Inspection Experts
"Protect Your Investment!"
11-Month Home Inspection Reminder
Don't Let Your Builder's Warranty Expire
Congratulations on your new home! As trusted home inspection experts, Pinecrest Home Inspections wants to ensure your peace of mind. Did you know that most builders offer a 1-year warranty on their construction? Now is the perfect time to schedule your 11-month inspection before your warranty expires.
Our comprehensive inspection will evaluate the key areas of your home to identify any potential issues covered under your builder's warranty. Our certified inspectors will thoroughly examine the structure, plumbing, electrical systems, HVAC, roofing, and more. Identifying these issues early can save you thousands of dollars in future repairs.
[Bullet Points]
- Early detection of hidden defects
- Maximize your builder's warranty coverage
- Protect your investment
- Ensure a safe and comfortable living environment
- Expert advice and recommendations
[Call to Action]
Schedule your 11-Month Inspection today!
Pinecrest Home Inspections
Your Partner in Home Ownership
[Back of the Postcard]
Why Choose Pinecrest Home Inspections?
[Bullet Points]
- Trusted industry professionals with over 20 years of experience
- Certified and licensed inspectors
- Thorough and comprehensive inspections
- Detailed inspection reports with photos
- Excellent customer service and support
- Competitive pricing and value
Pinecrest Home Inspections
847 SW 31st Ave, Ocala, FL USA
Visit: www.pinecresthomeinspections.com
Remember, time is of the essence! Schedule your 11-month inspection today to ensure your builder addresses any issues covered under warranty. We look forward to helping you protect your investment and enjoy your new home worry-free!
Sincerely,
Pinecrest Home Inspections
352-781-6094
Target Market(s)
New Home Owners
Industry/Entity Type
Inspections
Requirements
Must have
- Our logo, phone number, website
Nice to have
- eye catching

```html
<!DOCTYPE html>
<html lang="en">
<head>
<meta charset="UTF-8">
<title>Pinecrest Home Inspections – 11-Month Inspection Postcard</title>
<link rel="stylesheet" href="https://fonts.googleapis.com/css2?family=Montserrat:wght@500;700;800;900&family=Open+Sans:wght@400;600;700&display=swap">
<style>
  :root{
    --navy:#14285a;
    --navy-deep:#0c1b42;
    --red:#d7262e;
    --red-deep:#a8161d;
    --white:#ffffff;
    --ink:#2b2f3a;
    --muted:#5b6272;
    --page:#f3f4f6;
    --sky:#9fc3e6;
    --wall:#c9b79a;
  }
  *{margin:0;padding:0;box-sizing:border-box}
  html,body{width:784px;height:1200px;overflow:hidden;background:var(--page)}
  body{font-family:"Open Sans",Arial,sans-serif;color:var(--ink);position:relative}
  .card{position:absolute;left:32px;width:720px;height:480px;background:var(--white);overflow:hidden;box-shadow:0 4px 14px rgba(0,0,0,.12)}
  .card--front{top:100px}
  .card--back{top:620px}
  .abs{position:absolute}
  .heading{font-family:"Montserrat",Arial,sans-serif;font-weight:800;text-transform:uppercase;line-height:1}

  /* brand lockup */
  .brand{display:flex;align-items:center;gap:7px}
  .brand__mark{width:14px;height:14px;background:var(--red)}
  .brand__name{font-family:"Montserrat",Arial,sans-serif;font-weight:800;font-size:14px;color:var(--navy);line-height:1.05;width:130px}

  /* front */
  .front__brand{left:26px;top:20px}
  .front__kicker{left:26px;top:62px;font-family:"Montserrat",Arial,sans-serif;font-weight:700;font-size:10px;color:var(--navy);letter-spacing:.3px;text-transform:uppercase}
  .front__title{left:26px;top:80px}
  .front__title .line1{font-size:34px;color:var(--navy)}
  .front__title .line2{font-size:42px;color:var(--red);margin-top:2px}
  .front__photos{right:0;top:0;width:360px;height:220px}
  .reminder{left:0;top:172px;height:26px;width:340px;background:var(--navy);clip-path:polygon(0 0,100% 0,92% 100%,0 100%);display:flex;align-items:center;padding-left:26px;color:var(--white);font-family:"Montserrat",Arial,sans-serif;font-weight:800;font-size:11.5px;letter-spacing:.4px;text-transform:uppercase}
  .reminder::after{content:"";position:absolute;left:322px;top:0;width:18px;height:26px;background:var(--red);clip-path:polygon(40% 0,100% 0,60% 100%,0 100%)}
  .front__warning{left:26px;top:210px;font-size:15px;color:var(--red)}
  .front__body{left:26px;top:234px;width:668px;display:grid;grid-template-columns:1fr 1fr;column-gap:22px;font-size:8.6px;line-height:1.45;color:var(--ink)}
  .front__benefits{left:26px;top:326px;width:668px;display:grid;grid-template-columns:1fr 1fr;column-gap:22px;row-gap:5px;list-style:none}
  .benefit{display:flex;align-items:center;gap:7px;font-size:9.5px;font-weight:600;color:var(--navy)}
  .benefit__dot{width:8px;height:8px;background:var(--red);flex:none}
  .front__band{left:0;bottom:0;width:720px;height:78px}
  .cta{left:26px;top:420px;color:var(--white)}
  .cta__small{font-family:"Montserrat",Arial,sans-serif;font-weight:700;font-size:11px;letter-spacing:.5px;text-transform:uppercase;color:#c8d3ee}
  .cta__big{font-size:21px;margin-top:4px}
  .cta__big span{color:var(--red)}
  .signoff{left:430px;top:428px;display:flex;align-items:center;gap:10px;color:var(--white)}
  .signoff__circle{width:30px;height:30px;border-radius:50%;background:var(--white)}
  .signoff__name{font-family:"Montserrat",Arial,sans-serif;font-weight:700;font-size:13px}
  .signoff__tag{font-size:10px;color:#c8d3ee;margin-top:2px}

  /* back */
  .back__panel{left:0;top:0;width:370px;height:480px;background:var(--navy)}
  .back__title{left:24px;top:24px;color:var(--white);font-size:19px;line-height:1.1}
  .back__title span{color:var(--red)}
  .back__list{left:24px;top:80px;width:330px;display:grid;grid-template-columns:1fr 1fr;column-gap:14px;row-gap:10px;list-style:none}
  .check{display:flex;gap:6px;align-items:flex-start;color:var(--white);font-size:9px;line-height:1.35}
  .check svg{flex:none;margin-top:1px}
  .years{left:150px;top:196px;width:330px;height:30px;background:var(--red);clip-path:polygon(6% 0,100% 0,94% 100%,0 100%);display:flex;align-items:center;justify-content:center;color:var(--white);font-size:15px;letter-spacing:.5px}
  .back__note{left:24px;top:238px;width:330px;color:#d6ddef;font-size:8.4px;line-height:1.45}
  .back__photos{left:24px;top:304px;width:322px;height:92px;display:grid;grid-template-columns:1fr 1fr;gap:8px}
  .photo{width:100%;height:100%}
  .photo--inspector{background:linear-gradient(160deg,var(--sky),#5d83b4 55%,#36507e)}
  .photo--house{background:linear-gradient(160deg,#b7d2ee,var(--wall) 60%,#8a7a62)}
  .back__contact{left:0;top:410px;width:370px;height:70px;background:var(--red);padding:10px 24px;color:var(--white);font-size:9.5px;line-height:1.55}
  .contact-row{display:flex;align-items:center;gap:7px}
  .contact-row strong{font-family:"Montserrat",Arial,sans-serif;font-weight:700}
  .back__brand{left:470px;top:30px;flex-direction:column;text-align:center}
  .back__brand .brand__name{font-size:15px;width:150px}
  .sincerely{left:400px;top:98px;width:290px;text-align:center;font-size:9px;color:var(--muted);line-height:1.5}
  .stamp{left:640px;top:26px;width:54px;height:62px;border:1.5px dashed #9aa1ae}
  .address-lines{left:420px;top:300px;width:270px}
  .address-lines div{height:1px;background:#9aa1ae;margin-bottom:32px}
</style>
</head>
<body>

<!-- FRONT -->
<section class="card card--front" aria-label="Postcard front">
  <svg class="abs front__photos" viewBox="0 0 360 220" aria-hidden="false">
    <defs>
      <linearGradient id="gHouse" x1="0" y1="0" x2="1" y2="1"><stop offset="0" stop-color="#b7d2ee"/><stop offset=".6" stop-color="#c9b79a"/><stop offset="1" stop-color="#7f705a"/></linearGradient>
      <linearGradient id="gLadder" x1="0" y1="0" x2="1" y2="1"><stop offset="0" stop-color="#a9c8e8"/><stop offset=".55" stop-color="#d9dde3"/><stop offset="1" stop-color="#8a96a8"/></linearGradient>
      <linearGradient id="gRoof" x1="0" y1="0" x2="1" y2="1"><stop offset="0" stop-color="#7fa4cf"/><stop offset="1" stop-color="#4c5f78"/></linearGradient>
    </defs>
    <polygon points="60,0 360,0 360,220 120,220" fill="var(--navy)"/>
    <g role="img" aria-label="Photo of a new home exterior"><polygon points="70,0 190,0 240,110 130,110" fill="url(#gHouse)"/></g>
    <g role="img" aria-label="Photo of an inspector on a ladder checking the roof line"><polygon points="198,0 360,0 360,210 250,210 185,60" fill="url(#gLadder)"/></g>
    <g role="img" aria-label="Photo of a home entryway"><polygon points="135,118 243,118 285,212 176,212" fill="url(#gRoof)"/></g>
    <polygon points="300,0 360,0 360,40" fill="var(--red)"/>
    <g role="img" aria-label="American flag corner"><polygon points="322,0 360,0 360,26" fill="var(--white)"/></g>
    <polygon points="60,0 70,0 130,220 120,220" fill="var(--red)"/>
  </svg>

  <div class="abs brand front__brand"><span class="brand__mark"></span><span class="brand__name">Pinecrest Home Inspections</span></div>
  <p class="abs front__kicker">Your Trusted Home Inspection Experts</p>
  <h1 class="abs front__title heading"><div class="line1">Protect Your</div><div class="line2">Investment!</div></h1>

  <div class="abs reminder">11-Month Home Inspection Reminder</div>
  <h2 class="abs front__warning heading">Don't Let Your Builder's Warranty Expire</h2>

  <div class="abs front__body">
    <p>Congratulations on your new home! As trusted home inspection experts, Pinecrest Home Inspections wants to ensure your peace of mind. Did you know that most builders offer a 1-year warranty on their construction? Now is the perfect time to schedule your 11-month inspection before your warranty expires.</p>
    <p>Our comprehensive inspection will evaluate the key areas of your home to identify any potential issues covered under your builder's warranty. Our certified inspectors will thoroughly examine the structure, plumbing, electrical systems, HVAC, roofing, and more. Identifying these issues early can save you thousands of dollars in future repairs.</p>
  </div>

  <ul class="abs front__benefits">
    <li class="benefit"><span class="benefit__dot"></span>Early detection of hidden defects</li>
    <li class="benefit"><span class="benefit__dot"></span>Ensure a safe and comfortable living environment</li>
    <li class="benefit"><span class="benefit__dot"></span>Maximize your builder's warranty coverage</li>
    <li class="benefit"><span class="benefit__dot"></span>Expert advice and recommendations</li>
    <li class="benefit"><span class="benefit__dot"></span>Protect your investment</li>
  </ul>

  <svg class="abs front__band" viewBox="0 0 720 78" aria-hidden="true">
    <rect x="0" y="0" width="720" height="78" fill="var(--navy)"/>
    <polygon points="360,0 392,0 360,78 328,78" fill="var(--red)"/>
    <polygon points="398,0 408,0 376,78 366,78" fill="var(--red-deep)"/>
    <rect x="0" y="0" width="720" height="3" fill="var(--red)"/>
  </svg>
  <div class="abs cta">
    <div class="cta__small">Schedule your 11-Month</div>
    <div class="cta__big heading">Inspection <span>Today!</span></div>
  </div>
  <div class="abs signoff">
    <span class="signoff__circle"></span>
    <div><div class="signoff__name">Pinecrest Home Inspections</div><div class="signoff__tag">Your Partner in Home Ownership</div></div>
  </div>
</section>

<!-- BACK -->
<section class="card card--back" aria-label="Postcard back">
  <div class="abs back__panel"></div>
  <h2 class="abs back__title heading">Why Choose<br><span>Pinecrest</span> Home Inspections?</h2>

  <ul class="abs back__list">
    <li class="check"><svg width="10" height="10" viewBox="0 0 10 10"><rect width="10" height="10" fill="var(--red)"/><path d="M2 5.2l2 2 4-4.4" stroke="#fff" stroke-width="1.5" fill="none"/></svg>Trusted industry professionals with over 20 years of experience</li>
    <li class="check"><svg width="10" height="10" viewBox="0 0 10 10"><rect width="10" height="10" fill="var(--red)"/><path d="M2 5.2l2 2 4-4.4" stroke="#fff" stroke-width="1.5" fill="none"/></svg>Detailed inspection reports with photos</li>
    <li class="check"><svg width="10" height="10" viewBox="0 0 10 10"><rect width="10" height="10" fill="var(--red)"/><path d="M2 5.2l2 2 4-4.4" stroke="#fff" stroke-width="1.5" fill="none"/></svg>Certified and licensed inspectors</li>
    <li class="check"><svg width="10" height="10" viewBox="0 0 10 10"><rect width="10" height="10" fill="var(--red)"/><path d="M2 5.2l2 2 4-4.4" stroke="#fff" stroke-width="1.5" fill="none"/></svg>Excellent customer service and support</li>
    <li class="check"><svg width="10" height="10" viewBox="0 0 10 10"><rect width="10" height="10" fill="var(--red)"/><path d="M2 5.2l2 2 4-4.4" stroke="#fff" stroke-width="1.5" fill="none"/></svg>Thorough and comprehensive inspections</li>
    <li class="check"><svg width="10" height="10" viewBox="0 0 10 10"><rect width="10" height="10" fill="var(--red)"/><path d="M2 5.2l2 2 4-4.4" stroke="#fff" stroke-width="1.5" fill="none"/></svg>Competitive pricing and value</li>
  </ul>

  <div class="abs years heading">20 Years of Experience</div>

  <p class="abs back__note">Remember, time is of the essence! Schedule your 11-month inspection today to ensure your builder addresses any issues covered under warranty. We look forward to helping you protect your investment and enjoy your new home worry-free!</p>

  <div class="abs back__photos">
    <div class="photo photo--inspector" role="img" aria-label="Photo of an inspector examining a home"></div>
    <div class="photo photo--house" role="img" aria-label="Photo of a newly built house"></div>
  </div>

  <div class="abs back__contact">
    <div class="contact-row"><svg width="10" height="10" viewBox="0 0 24 24"><path fill="#fff" d="M6.6 10.8a15.1 15.1 0 006.6 6.6l2.2-2.2a1 1 0 011-.25 11.4 11.4 0 003.6.57 1 1 0 011 1V20a1 1 0 01-1 1A17 17 0 013 4a1 1 0 011-1h3.5a1 1 0 011 1 11.4 11.4 0 00.57 3.6 1 1 0 01-.25 1z"/></svg><strong>352-781-6094</strong></div>
    <div class="contact-row"><svg width="10" height="10" viewBox="0 0 24 24"><circle cx="12" cy="12" r="9" fill="none" stroke="#fff" stroke-width="2"/><path d="M3 12h18M12 3c3 3 3 15 0 18M12 3c-3 3-3 15 0 18" stroke="#fff" stroke-width="1.6" fill="none"/></svg>Visit: www.pinecresthomeinspections.com</div>
    <div class="contact-row"><svg width="10" height="10" viewBox="0 0 24 24"><path fill="#fff" d="M12 2a7 7 0 00-7 7c0 5 7 13 7 13s7-8 7-13a7 7 0 00-7-7zm0 9.5A2.5 2.5 0 1112 6.5a2.5 2.5 0 010 5z"/></svg>847 SW 31st Ave, Ocala, FL USA</div>
  </div>

  <div class="abs brand back__brand"><span class="brand__mark"></span><span class="brand__name">Pinecrest Home Inspections</span></div>
  <p class="abs sincerely">Sincerely, Pinecrest Home Inspections · 352-781-6094<br>www.PinecrestHomeInspections.com</p>
  <div class="abs stamp"></div>
  <div class="abs address-lines"><div></div><div></div><div></div><div></div></div>
</section>

</body>
</html>
```